Website redesign www.marigoldlawpc.com law firm site

Need to redesign the website that I currently have to look more modern and professional. Would also like to be able to make updates and post without having a huge hassle. See current www.marigoldlawpc.com. I just think that it looks very immature and it's very templated there's no ability for me to make posts or Add links or anything like that

Target Market(s)

California people looking for a powerhouse attorney in

Industry/Entity Type

Legal

Number of Pages Required

3 page

Font styles to use
Serif
Sans Serif

Colors
ec1f27
000000
ffffff

Requirements
Must have
• Must be mobile friendly. Must look professional and have ability to post links to other websites. Must have ability to post blogs or articles. Would like to be able to read my FeeTrove account and also have the ability to upload forms for people to download
Nice to have
• Simple design easy to use and not cluttered with too much text

```html
<!DOCTYPE html>
<html lang="en">
<head>
<meta charset="utf-8">
<title>Marigold Law, P.C. — Chico California Attorney</title>
<link rel="stylesheet" href="https://fonts.googleapis.com/css2?family=Cinzel:wght@400;600;700&family=Open+Sans:ital,wght@0,400;0,600;0,700;1,400&display=swap">
<style>
:root{
  --red:#ec1f27;
  --black:#000000;
  --ink:#1d1d1d;
  --text:#555555;
  --white:#ffffff;
  --bar:#f4f4f4;
  --card:#3c3c3c;
  --band:#141414;
  --line:#e2e2e2;
}
*{box-sizing:border-box;margin:0;padding:0}
html,body{width:1200px;height:2575px;overflow:hidden}
body{font-family:"Open Sans",Arial,sans-serif;color:var(--text);background:var(--white)}
.wrap{width:1050px;margin:0 auto;position:relative;height:100%}
a{color:inherit;text-decoration:none}

/* top bar */
.topbar{height:52px;background:var(--bar);border-bottom:1px solid var(--line);font-size:12.5px;color:#333}
.topbar .wrap{display:flex;align-items:center;justify-content:space-between}
.topbar .info{display:flex;align-items:center;gap:8px}
.topbar .info span{display:flex;align-items:center;gap:6px}
.topbar .contact{color:var(--red)}
.topbar svg{width:12px;height:12px}
.sep{color:#999}

/* nav */
.nav{height:72px;background:var(--white);box-shadow:0 1px 3px rgba(0,0,0,.08);position:relative;z-index:2}
.nav .wrap{display:flex;align-items:center;justify-content:space-between}
.brand{color:var(--red);font-family:"Cinzel",Georgia,serif;font-size:24px;font-weight:600;white-space:nowrap;line-height:72px}
.menu{display:flex;height:72px;align-items:stretch}
.menu a{font-family:"Cinzel",Georgia,serif;font-size:14px;color:#222;display:flex;align-items:center;padding:0 15px;position:relative;white-space:nowrap}
.menu a.active{color:var(--red)}
.menu a.active::after{content:"";position:absolute;left:2px;right:2px;bottom:6px;height:4px;background:var(--red)}
.menu a svg{width:9px;height:9px;margin-left:8px}
.menu a:last-child{padding-right:0}

/* hero */
.hero{height:534px;position:relative;background:linear-gradient(180deg,#8da1b8 0%,#6f7f92 35%,#3d4756 70%,#2a313b 100%)}
.hero-title{position:absolute;top:200px;left:0;right:0;text-align:center;color:var(--white);font-family:"Cinzel",Georgia,serif;font-weight:400;font-size:54px;line-height:60px;letter-spacing:1px;text-shadow:0 2px 6px rgba(0,0,0,.4)}
.dots{position:absolute;top:469px;left:0;right:0;display:flex;justify-content:center;gap:4px}
.dots i{width:14px;height:14px;border-radius:50%;background:#1b1b1b}
.dots i.on{background:var(--red)}

/* welcome */
.welcome{height:327px;text-align:center;border-bottom:1px solid var(--line)}
.welcome h2{font-family:"Cinzel",Georgia,serif;font-weight:600;color:var(--ink);font-size:24px;padding-top:40px;line-height:30px}
.welcome h3{font-family:"Cinzel",Georgia,serif;font-weight:400;color:var(--red);font-size:28px;line-height:34px;word-spacing:3px}
.welcome p{font-size:14px;line-height:25px;width:1030px;margin:20px auto 0;color:#555}
.btn{display:inline-block;background:var(--black);color:var(--white);font-family:"Cinzel",Georgia,serif;font-weight:600;font-size:13px;height:41px;line-height:41px;width:153px;text-align:center}
.welcome .btn{margin-top:34px}

/* practice */
.practice{height:495px;position:relative}
.practice .photo{position:absolute;left:0;top:0;width:419px;height:495px;background:linear-gradient(135deg,#eef0f2 0%,#c9d1dc 45%,#8ea3bd 75%,#e9e6e2 100%)}
.practice .head{position:absolute;left:447px;top:38px;width:680px;display:flex;justify-content:space-between;align-items:center}
.practice h2{font-family:"Cinzel",Georgia,serif;font-weight:400;font-size:27px;color:var(--red)}
.arrows{display:flex;gap:12px}
.arrows svg{width:12px;height:18px}
.cards{position:absolute;left:448px;top:93px;display:grid;grid-template-columns:332px 332px;column-gap:15px;row-gap:19px}
.card{background:var(--card);height:175px;padding:18px 20px;color:#ddd}
.card .title{display:flex;align-items:center;gap:18px;margin-bottom:14px}
.card .icon{width:55px;height:52px;background:var(--white);display:flex;align-items:center;justify-content:center}
.card .icon svg{width:32px;height:32px}
.card h3{font-family:"Cinzel",Georgia,serif;font-weight:400;font-size:22px;color:var(--white)}
.card p{font-size:13px;line-height:23px}

/* reviews */
.reviews{height:368px;background:linear-gradient(160deg,#8a0a10 0%,#c4151d 40%,var(--red) 60%,#9a0d13 85%,#d01820 100%);text-align:center;color:var(--white)}
.reviews h2{font-family:"Cinzel",Georgia,serif;font-weight:400;font-size:25px;padding-top:43px;letter-spacing:.5px}
.reviews h4{font-weight:600;font-size:18px;margin-top:22px}
.reviews blockquote{font-style:italic;font-size:15px;line-height:33px;width:1070px;margin:8px auto 0}
.reviews cite{display:block;font-style:normal;font-weight:700;font-size:14px;margin-top:12px}
.reviews .btn{margin-top:35px}

/* blog */
.blog{height:463px}
.blog h2{text-align:center;font-family:"Cinzel",Georgia,serif;font-weight:400;font-size:27px;color:var(--red);padding-top:47px;line-height:32px}
.posts{display:grid;grid-template-columns:repeat(3,329px);column-gap:31px;margin-top:30px}
.thumb{height:194px;border:3px solid #ddd}
.thumb.t1{background:linear-gradient(135deg,#f4eeea,#caa5a0 50%,#7a1a1f)}
.thumb.t2{background:linear-gradient(135deg,#dfe6ee,#9fb0c2 50%,#3a3f48)}
.thumb.t3{background:linear-gradient(135deg,#c8ccd2,#6f7680 50%,#262a30)}
.post h3{font-family:"Cinzel",Georgia,serif;font-weight:600;color:var(--ink);font-size:16px;margin-top:17px}
.post p{font-size:14px;line-height:25px;margin-top:4px;color:#666}
.post a{display:block;color:var(--red);font-size:12px;margin-top:9px}

/* info band */
.band{height:144px;background:var(--band)}
.band .wrap{display:flex;justify-content:space-between;align-items:center}
.band p{width:715px;font-size:11.5px;line-height:22px;color:#cfcfcf}
.partner{width:302px;height:89px;border:1px solid #555;display:flex;align-items:center;justify-content:center;color:var(--white);font-family:"Cinzel",Georgia,serif;font-size:22px;white-space:nowrap}

/* footer */
.footer{height:120px;background:var(--red);color:var(--white)}
.footer .wrap{display:flex;justify-content:space-between}
.fnav{display:flex;gap:30px;font-weight:700;font-size:12px;margin-top:30px}
.copy{font-size:12px;margin-top:25px}
.copy .sep{color:#fff;margin:0 8px}
.follow{width:165px;margin-top:30px}
.follow h5{font-size:12px;font-weight:700}
.social{display:flex;gap:8px;margin-top:10px}
.social i{width:29px;height:29px;border-radius:50%;background:var(--white)}
</style>
</head>
<body>

<header class="topbar">
  <div class="wrap">
    <div class="info">
      <span><svg viewBox="0 0 12 12"><path d="M6 0a4 4 0 0 0-4 4c0 3 4 8 4 8s4-5 4-8a4 4 0 0 0-4-4zm0 5.6A1.6 1.6 0 1 1 6 2.4a1.6 1.6 0 0 1 0 3.2z" fill="#333"/></svg>48 Orchard Lane, Suite 210 Chico, CA 95926</span>
      <span class="sep">|</span>
      <span><svg viewBox="0 0 12 12"><rect x="1" y="3" width="10" height="7" rx="1" fill="#333"/><rect x="3" y="1" width="6" height="3" fill="#333"/><rect x="3" y="5" width="6" height="1.4" fill="#f4f4f4"/></svg>(555) 014-2290</span>
    </div>
    <div class="info contact">
      <span><svg viewBox="0 0 12 12"><path d="M2.4 1l2 2.3-1.1 1.3a7 7 0 0 0 4.1 4.1l1.3-1.1 2.3 2-1.3 1.4C5.2 10.6 1.4 6.8.9 2.3z" fill="#ec1f27"/></svg>(555) 013-4471</span>
      <span class="sep">|</span>
      <span><svg viewBox="0 0 12 12"><rect x="0.5" y="2" width="11" height="8" fill="#ec1f27"/><path d="M0.5 2.5L6 6.5l5.5-4" stroke="#fff" stroke-width="1" fill="none"/></svg>dana@marigoldlawgroup.com</span>
    </div>
  </div>
</header>

<nav class="nav">
  <div class="wrap">
    <a class="brand" href="#">Marigold Law, P.C.</a>
    <div class="menu">
      <a class="active" href="#">Home</a>
      <a href="#">Attorney Profile</a>
      <a href="#">Practice Areas<svg viewBox="0 0 10 10"><path d="M1 3l4 4 4-4" stroke="#222" stroke-width="1.4" fill="none"/></svg></a>
      <a href="#">Client Reviews</a>
      <a href="#">Links</a>
      <a href="#">Contact Us</a>
    </div>
  </div>
</nav>

<section class="hero" role="img" aria-label="City skyline with downtown towers beside the bay">
  <h1 class="hero-title">Marigold Law, P.C.<br>Chico California Attorney</h1>
  <div class="dots" aria-hidden="true"><i class="on"></i><i></i><i></i><i></i></div>
</section>

<section class="welcome">
  <h2>Welcome to</h2>
  <h3>Marigold Law, P.C.&nbsp; Chico California Attorney</h3>
  <p>Marigold Law P.C. is owned by Dana L. Marigold, a dedicated and caring professional who uses her broad range of skills as a California lawyer to bring consumers and business owners exceptionally strong legal representation that achieves best results. She works with people from across the northern region of California, from the Northern border to the Central Valley region</p>
  <a class="btn" href="#">Read More</a>
</section>

<section class="practice">
  <div class="photo" role="img" aria-label="Attorney reviewing documents with a client at a desk"></div>
  <div class="head">
    <h2>Practice Areas</h2>
    <div class="arrows">
      <svg viewBox="0 0 12 18"><path d="M9 2L3 9l6 7" stroke="#222" stroke-width="1.6" fill="none"/></svg>
      <svg viewBox="0 0 12 18"><path d="M3 2l6 7-6 7" stroke="#ec1f27" stroke-width="1.6" fill="none"/></svg>
    </div>
  </div>
  <div class="cards">
    <article class="card">
      <div class="title"><span class="icon"><svg viewBox="0 0 32 32"><rect x="3" y="9" width="26" height="19" rx="2" fill="#ec1f27"/><path d="M11 9V6h10v3" stroke="#ec1f27" stroke-width="2.5" fill="none"/></svg></span><h3>Business Law</h3></div>
      <p>Vestibulum ante ipsum primis in faucibus orci luctus et ultrices posuere. Aenean a nibh eget turpis vehicula tempus ac sed massa...</p>
    </article>
    <article class="card">
      <div class="title"><span class="icon"><svg viewBox="0 0 32 32"><path d="M16 4L2 16h4v12h8v-8h4v8h8V16h4z" fill="#ec1f27"/></svg></span><h3>Real Estate Law</h3></div>
      <p>Vestibulum ante ipsum primis in faucibus orci luctus et ultrices posuere. Aenean a nibh eget turpis vehicula tempus ac sed massa...</p>
    </article>
    <article class="card">
      <div class="title"><span class="icon"><svg viewBox="0 0 32 32"><circle cx="16" cy="9" r="5" fill="#ec1f27"/><circle cx="7" cy="12" r="3.5" fill="#ec1f27"/><circle cx="25" cy="12" r="3.5" fill="#ec1f27"/><path d="M8 27c0-6 3-11 8-11s8 5 8 11z" fill="#ec1f27"/><path d="M1 26c0-5 2-9 6-9 2 0 3 1 3 1l-2 8zM31 26c0-5-2-9-6-9-2 0-3 1-3 1l2 8z" fill="#ec1f27"/></svg></span><h3>Family Law</h3></div>
      <p>Vestibulum ante ipsum primis in faucibus orci luctus et ultrices posuere. Aenean a nibh eget turpis vehicula tempus ac sed massa...</p>
    </article>
    <article class="card">
      <div class="title"><span class="icon"><svg viewBox="0 0 32 32"><path d="M16 2L2 9v2h28V9z" fill="#ec1f27"/><rect x="5" y="13" width="3" height="11" fill="#ec1f27"/><rect x="11" y="13" width="3" height="11" fill="#ec1f27"/><rect x="18" y="13" width="3" height="11" fill="#ec1f27"/><rect x="24" y="13" width="3" height="11" fill="#ec1f27"/><rect x="2" y="26" width="28" height="4" fill="#ec1f27"/></svg></span><h3>Bankruptcy</h3></div>
      <p>Vestibulum ante ipsum primis in faucibus orci luctus et ultrices posuere. Aenean a nibh eget turpis vehicula tempus ac sed massa...</p>
    </article>
  </div>
</section>

<section class="reviews">
  <h2>Client Reviews</h2>
  <h4>Exceeded Our Expectations</h4>
  <blockquote>“ Marigold Law has met and exceeded our expectations in assisting our company with our real estate legal needs. In an area of law where the rules our ever changing, we simply could not navigate our company effectively without their help...”</blockquote>
  <cite>- Alder Ridge Commercial</cite>
  <a class="btn" href="#">Read More</a>
</section>

<section class="blog">
  <h2>Blog Posts</h2>
  <div class="wrap posts" style="height:auto">
    <article class="post">
      <div class="thumb t1" role="img" aria-label="Word cloud on the theme of criminal law"></div>
      <h3>Lorem ipsum dolor sit amet</h3>
      <p>Vestibulum ante ipsum primis in faucibus orci luctus et ultrices posuere cubilia..</p>
      <a href="#">Continue Reading</a>
    </article>
    <article class="post">
      <div class="thumb t2" role="img" aria-label="Business team meeting around a laptop"></div>
      <h3>Lorem ipsum dolor sit amet</h3>
      <p>Vestibulum ante ipsum primis in faucibus orci luctus et ultrices posuere cubilia..</p>
      <a href="#">Continue Reading</a>
    </article>
    <article class="post">
      <div class="thumb t3" role="img" aria-label="Professionals signing papers at a table"></div>
      <h3>Lorem ipsum dolor sit amet</h3>
      <p>Vestibulum ante ipsum primis in faucibus orci luctus et ultrices posuere cubilia..</p>
      <a href="#">Continue Reading</a>
    </article>
  </div>
</section>

<section class="band">
  <div class="wrap">
    <p>Marigold Law, P.C. provides experienced, compassionate legal guidance and representation to businesses and individuals in the areas of business law, real estate law, bankruptcy, family law, criminal law, civil litigation, unlawful detainer, and legal document preparation. Located in Chico, California, we serve clients throughout Northern California including Butte County, Tehama County, Plumas County, Glenn County, Colusa County, Sutter County, Yuba County, Sierra County and Nevada County.</p>
    <div class="partner">Westline Properties</div>
  </div>
</section>

<footer class="footer">
  <div class="wrap">
    <div>
      <div class="fnav"><a href="#">HOME</a><a href="#">ATTORNEY PROFILE</a><a href="#">PRACTICE AREAS</a><a href="#">CLIENT REVIEWS</a><a href="#">LINKS</a><a href="#">CONTACT US</a></div>
      <div class="copy">© 2016 Marigold Law, P.C. All Right Reserved<span class="sep">|</span>Disclaimer<span class="sep">|</span>Site Map<span class="sep">|</span>Sign In</div>
    </div>
    <div class="follow">
      <h5>FOLLOW US</h5>
      <div class="social"><i></i><i></i><i></i><i></i><i></i></div>
    </div>
  </div>
</footer>

</body>
</html>
```